Flyers

Modify Existing Flyer and create another for exterior company
Updates

Previous Brief has been updated- we want to update this existing one also

Target Market(s)

Exterior Remodeling Customers

Industry/Entity Type

Remodeling/Construction

```html
<!DOCTYPE html>
<html lang="en">
<head>
<meta charset="utf-8">
<title>Northvale Roofing and Exteriors – Remodeling Flyer</title>
<link href="https://fonts.googleapis.com/css2?family=Lato:wght@400;700;900&family=Oswald:wght@500&display=swap" rel="stylesheet">
<style>
  :root {
    --orange: #ee5a24;
    --orange-deep: #e04e1a;
    --navy: #232d37;
    --ink: #111111;
    --text: #2b2b2b;
    --card-line: #e4e4e4;
    --page-bg: #ecebe8;
    --white: #ffffff;
    --sky: #2f8fd8;
  }
  * { box-sizing: border-box; margin: 0; padding: 0; }
  html, body {
    width: 1200px; height: 1200px; overflow: hidden;
    background: var(--page-bg);
    font-family: "Lato", Arial, sans-serif;
    color: var(--text);
  }
  .flyer {
    position: absolute; left: 184px; top: 20px;
    width: 832px; height: 1160px;
    background: var(--white);
    box-shadow: 0 4px 18px rgba(0,0,0,.18);
    overflow: hidden;
  }
  .hero-photo {
    position: absolute; left: 0; top: 0; width: 832px; height: 600px;
    background:
      linear-gradient(180deg, rgba(255,255,255,0) 70%, #fff 100%),
      linear-gradient(100deg, #d8d9d8 0%, #f4f4f3 30%, #fbfbfb 55%, #e9e8e6 80%, #cfcecb 100%);
  }
  .brand-banner {
    position: absolute; left: 17px; top: 0; width: 296px; height: 250px;
    background: var(--navy);
    clip-path: polygon(0 0, 100% 0, 100% 76%, 50% 100%, 0 76%);
    display: flex; flex-direction: column; align-items: center;
    padding-top: 70px;
  }
  .brand-name {
    display: flex; align-items: center; gap: 10px;
    font-weight: 900; font-size: 40px; color: var(--orange); letter-spacing: 1px;
  }
  .brand-mark { width: 22px; height: 22px; background: var(--orange); }
  .brand-tagline {
    margin-top: 14px; padding: 4px 0;
    border-top: 1px solid var(--sky); border-bottom: 1px solid var(--sky);
    font-size: 17px; font-weight: 400; color: var(--white); letter-spacing: .5px;
  }
  .estimate-call {
    position: absolute; right: 0; top: 19px; height: 40px;
    display: flex; align-items: stretch;
  }
  .estimate-label {
    background: var(--white); padding: 2px 12px 0 12px; text-align: right;
    color: var(--orange); line-height: 1.05;
  }
  .estimate-label .lead { font-size: 15px; font-weight: 400; display: block; }
  .estimate-label .offer { font-size: 19px; font-weight: 900; display: block; }
  .phone-band {
    background: var(--navy); padding: 0 16px 0 26px; margin-left: -10px;
    clip-path: polygon(12px 0, 100% 0, 100% 100%, 0 100%);
    display: flex; align-items: center; gap: 6px;
    font-family: "Oswald", "Arial Narrow", sans-serif; font-weight: 500;
    font-size: 28px; color: var(--orange);
  }
  .headline {
    position: absolute; left: 22px; top: 274px;
    font-weight: 900; color: var(--ink); text-transform: uppercase; line-height: 1;
  }
  .headline .line { display: inline-block; font-size: 40px; letter-spacing: .5px; padding: 2px 6px; }
  .headline .line-accent { background: var(--orange); color: var(--white); margin: 3px 0; }
  .headline .subline {
    display: inline-block; margin-top: 2px; padding: 6px 8px 4px;
    background: var(--orange); color: var(--white);
    font-size: 20px; font-weight: 700; letter-spacing: .2px;
  }
  .service {
    position: absolute; left: 18px; width: 790px;
    display: flex; gap: 14px;
  }
  .service-photo {
    width: 286px; flex: none;
    border: 5px solid var(--white);
    box-shadow: 0 0 0 1px var(--card-line), 0 2px 5px rgba(0,0,0,.12);
  }
  .service-card {
    flex: 1; background: var(--white);
    border: 4px solid var(--card-line);
    padding: 9px 14px 6px;
  }
  .service-title {
    font-size: 22px; font-weight: 900; color: var(--ink); text-transform: uppercase; line-height: 1;
  }
  .service-title .accent { color: var(--orange); border-bottom: 2px solid var(--orange); }
  .service-intro { font-size: 10.5px; line-height: 1.35; margin-top: 6px; color: var(--text); }
  .checklist {
    list-style: none; margin-top: 8px;
    display: grid; grid-template-columns: 1fr 1fr; column-gap: 20px; row-gap: 1px;
    grid-auto-flow: column;
  }
  .checklist.single { grid-template-columns: 1fr; grid-auto-flow: row; }
  .checklist li {
    position: relative; padding-left: 14px; font-size: 10.5px; color: var(--text); line-height: 1.3;
  }
  .checklist li::before {
    content: ""; position: absolute; left: 0; top: 3px; width: 9px; height: 9px;
    border: 1px solid var(--orange);
  }
  .checklist li::after {
    content: ""; position: absolute; left: 3px; top: 4px; width: 3px; height: 5px;
    border: solid var(--orange); border-width: 0 1.5px 1.5px 0; transform: rotate(45deg);
  }
  .service-kitchen { top: 478px; height: 166px; }
  .service-additions { top: 652px; height: 150px; }
  .service-bath { top: 810px; height: 150px; }
  .service-patio { top: 968px; height: 148px; }
  .photo-kitchen { background: linear-gradient(180deg, #f2f2f2 0%, #e6e4e0 55%, #3a3a3a 75%, #b88a5e 100%); }
  .photo-living { background: linear-gradient(90deg, #d9462a 0%, #e9c27a 40%, #c9a06a 70%, #8b6a44 100%); }
  .photo-bath { background: linear-gradient(90deg, #bfc3c6 0%, #e8e9ea 45%, #d5d5d5 75%, #6a8a58 100%); }
  .photo-patio { background: linear-gradient(180deg, #6f7c5a 0%, #8a9a64 50%, #5e8c3a 75%, #c9c3b5 100%); }
  .footer-band {
    position: absolute; left: 0; bottom: 0; width: 832px; height: 36px;
    background: linear-gradient(90deg, var(--orange-deep), var(--orange));
    display: flex; align-items: center; justify-content: center;
    color: var(--white); font-weight: 700; font-size: 20px; letter-spacing: .3px;
    padding-right: 60px;
  }
</style>
</head>
<body>
<main class="flyer">
  <div class="hero-photo" role="img" aria-label="Bright white kitchen with marble island, black-framed windows and bar stools"></div>

  <header class="brand-banner">
    <div class="brand-name"><span class="brand-mark"></span>NORTHVALE</div>
    <div class="brand-tagline">ROOFING AND EXTERIORS</div>
  </header>

  <div class="estimate-call">
    <div class="estimate-label">
      <span class="lead">CALL TODAY FOR YOUR</span>
      <span class="offer">FREE ESTIMATE</span>
    </div>
    <div class="phone-band">
      <svg width="16" height="26" viewBox="0 0 16 26" aria-hidden="true">
        <rect x="1.5" y="1.5" width="13" height="23" rx="2.5" fill="none" stroke="#fff" stroke-width="2"/>
        <line x1="6" y1="21" x2="10" y2="21" stroke="#fff" stroke-width="1.5"/>
      </svg>
      <span>+ 555-014-2290</span>
    </div>
  </div>

  <section class="headline">
    <span class="line">Ready for a</span><br>
    <span class="line line-accent">Beautiful &amp; Functional</span><br>
    <span class="line">Kitchen or Bathroom?</span><br>
    <span class="subline">Work with a top rated local remodeling company in Riverton, IA</span>
  </section>

  <article class="service service-kitchen">
    <div class="service-photo photo-kitchen" role="img" aria-label="Modern white kitchen with black island and pendant lights"></div>
    <div class="service-card">
      <h2 class="service-title"><span class="accent">Kitchen</span> Remodeling</h2>
      <p class="service-intro">Whatever your vision is for your new kitchen, our crew can help you bring it to life. You can trust us for:</p>
      <ul class="checklist" style="grid-template-rows:repeat(5,auto)">
        <li>Open concept design services</li>
        <li>Kitchen cabinet installation services</li>
        <li>Kitchen countertop installation services</li>
        <li>Tile installation services</li>
        <li>Lighting installation services</li>
        <li>Plumbing upgrade services</li>
        <li>Electrical upgrade services</li>
        <li>Drywall services</li>
        <li>Painting services</li>
      </ul>
    </div>
  </article>

  <article class="service service-additions">
    <div class="service-photo photo-living" role="img" aria-label="Open living room with sofa, orange wall and wood kitchen"></div>
    <div class="service-card">
      <h2 class="service-title"><span class="accent">Home</span> Additions</h2>
      <p class="service-intro">No matter what kind of space you need, our team will bring your vision to life. You can hire us if you need a:</p>
      <ul class="checklist" style="grid-template-rows:repeat(4,auto)">
        <li>Bathroom addition</li>
        <li>Bedroom addition</li>
        <li>Garage addition</li>
        <li>Basement addition</li>
        <li>Guest room addition</li>
        <li>Living room addition</li>
        <li>Sunroom addition</li>
      </ul>
    </div>
  </article>

  <article class="service service-bath">
    <div class="service-photo photo-bath" role="img" aria-label="Bright bathroom with grey vanity and glass tile shower"></div>
    <div class="service-card">
      <h2 class="service-title"><span class="accent">Bathroom</span> Remodeling</h2>
      <p class="service-intro">When you hire us for your bathroom remodeling project, the possibilities are endless. Our experienced and talented team can:</p>
      <ul class="checklist single">
        <li>Install a custom tile shower</li>
        <li>Build a new vanity</li>
        <li>Install flooring and tile</li>
        <li>Replace your plumbing and light fixtures</li>
      </ul>
    </div>
  </article>

  <article class="service service-patio">
    <div class="service-photo photo-patio" role="img" aria-label="Garden patio with olive trees, lounge chairs and lawn"></div>
    <div class="service-card">
      <h2 class="service-title"><span class="accent">Decks/</span>Patios</h2>
      <p class="service-intro">An outdoor space is a great addition to any residential property. When you decide to build a patio or deck, you'll be able to experience a variety of benefits. Your outdoor area will increase your:</p>
      <ul class="checklist single">
        <li>Property value</li>
        <li>Curb appeal</li>
        <li>Functional living space</li>
      </ul>
    </div>
  </article>

  <footer class="footer-band">www.northvalehomes.com</footer>
</main>
</body>
</html>
```